Business card design needed

I would like a one sided black business card with the information provided above. Refer to my website www.brightvolleyracquets.com.au for an example of colors I have used for my site, would like to keep this consistent for my business cards also, I will upload my logo below.

I am a new small business that provides tennis customers with racquet re stringing, tennis strings and accessories.

Industry/Entity Type

Small Business

Contact Information for Business Card

Bright Volley Tennis

Owen Whitby
Managing Director

brightvolleyracquets@mailbox.example
www.brightvolleyracquets.com.au
0491 726 305

Racquet Restringing/Tennis Strings/Accessories

Requirements
Must have
• Must have my logo and card must be black

```html
<!DOCTYPE html>
<html lang="en">
<head>
<meta charset="utf-8">
<title>Bright Volley Tennis – Business Card</title>
<link rel="stylesheet" href="https://fonts.googleapis.com/css2?family=Roboto:wght@400;700&display=swap">
<style>
  :root {
    --stage: #e9e6e1;
    --card-black: #000000;
    --lime: #b6d433;
    --navy: #2b578a;
    --white: #ffffff;
    --ink: #1a1a1a;
    --muted: #d9d9d9;
  }
  * { box-sizing: border-box; margin: 0; padding: 0; }
  html, body {
    width: 1200px;
    height: 475px;
    overflow: hidden;
    background: var(--stage);
    font-family: "Roboto", Arial, sans-serif;
  }
  .card-set {
    position: absolute;
    inset: 0;
    display: flex;
    gap: 20px;
    justify-content: center;
    align-items: center;
  }
  .card {
    position: relative;
    width: 525px;
    height: 300px;
    background: var(--card-black);
    overflow: hidden;
  }
  .brand {
    position: absolute;
    display: flex;
    align-items: center;
    gap: 10px;
    color: var(--lime);
    font-weight: 700;
    font-size: 26px;
    letter-spacing: 0.5px;
    text-transform: uppercase;
    white-space: nowrap;
  }
  .brand-dot {
    width: 30px;
    height: 30px;
    border-radius: 50%;
    background: var(--lime);
    flex: none;
  }
  .card--front .brand { left: 30px; top: 78px; }
  .card--back .brand { left: 50%; top: 120px; transform: translateX(-50%); }

  .contact {
    position: absolute;
    left: 30px;
    top: 168px;
    list-style: none;
    color: var(--white);
    font-size: 14px;
    line-height: 19px;
    font-weight: 400;
  }
  .accent-band {
    position: absolute;
    left: 0;
    right: 0;
    bottom: 0;
    height: 62px;
    background: linear-gradient(90deg, var(--navy) 0%, var(--navy) 30%, var(--lime) 70%, var(--lime) 100%);
  }
  .holder {
    position: absolute;
    right: 24px;
    bottom: 12px;
    color: var(--ink);
    text-align: left;
  }
  .holder-name {
    font-size: 20px;
    font-weight: 400;
    text-transform: uppercase;
    letter-spacing: 0.3px;
    line-height: 22px;
  }
  .holder-role {
    font-size: 13px;
    font-weight: 400;
    line-height: 18px;
  }
  .web {
    position: absolute;
    left: 0;
    right: 0;
    top: 250px;
    text-align: center;
    color: var(--muted);
    font-size: 13px;
    letter-spacing: 1.6px;
  }
</style>
</head>
<body>
  <main class="card-set">
    <section class="card card--front" aria-label="Card front">
      <div class="accent-band" role="img" aria-label="Decorative wave band in navy, white and lime"></div>
      <div class="brand"><span class="brand-dot"></span>Bright Volley Tennis</div>
      <ul class="contact">
        <li>P : 0491 726 305</li>
        <li>E : brightvolleyracquets@mailbox.example</li>
        <li>W: www.brightvolleyracquets.com.au</li>
      </ul>
      <div class="holder">
        <p class="holder-name">Owen Whitby</p>
        <p class="holder-role">Managing Director</p>
      </div>
    </section>

    <section class="card card--back" aria-label="Card back">
      <div class="brand"><span class="brand-dot"></span>Bright Volley Tennis</div>
      <p class="web">www.brightvolleyracquets.com.au</p>
    </section>
  </main>
</body>
</html>
```